Design for a real estate wev portal

Contents and features of the site
---------------------------------
Website in 5 languages: French, Dutch, English, German, Spanish.
English name of the site: Harbor Nest Place
Main purpose of the site:
- allow people to rent their house/ appartment for flatsharing purposes.
- help people wanting to find a room in flatsharing
- help people to find additional roommates for their flatsharing
Key interaction sequence:
1. I create a "group" of people who have common interest/hobbies
2. People who have the same interests/hobbies join my group
3. I look for a house/appartment to host my group
Website structure will be the following:
- Home
- Groups
-- Look for a group
--- Join a group
-- Create a group
- Properties
-- Look for a house/appartement
-- Apply
- Sales conditions
- Contact
- My account
-- My profile
-- My groups OR my properties
Your mission
------------
The client has no graphical guidelines, simply a logo (see attached).
We need a (responsive compliant) design for the following pages (we expect PSD's from you. No HTML nor CSS):
1. homepage (see example and wireframe attached)
2. properties search result list (see wireframe attached)
3. "detailed" form for properties
4. groups search result list
5. "detailed" form for groups
6. my account page
FOR THE COMPETITION step we only expect from you the design of first 2 screens.
Based on that, we will select the designer who will win the project, and will have to design the 4 remaining screens.
Target Market(s)
B2C
Industry/Entity Type
Real Estate
Number of Pages Required
5+ page
Look and feel
Each slider illustrates characteristics of the customer's brand and the style your logo design should communicate.

```html
<!DOCTYPE html>
<html lang="en">
<head>
<meta charset="utf-8">
<title>Harbor Nest Place — Home</title>
<link href="https://fonts.googleapis.com/css2?family=Open+Sans:wght@400;600;700&display=swap" rel="stylesheet">
<style>
  :root{
    --teal:#2ba3b8;
    --green:#6abf45;
    --ink:#2b2b2b;
    --text:#555555;
    --muted:#7a7a7a;
    --panel:#f3f3f3;
    --line:#dcdcdc;
    --footer:#2d2d2d;
    --white:#ffffff;
  }
  *{box-sizing:border-box;margin:0;padding:0}
  html,body{width:1200px;height:2643px;overflow:hidden;background:var(--white)}
  body{font-family:"Open Sans",Arial,sans-serif;color:var(--text);position:relative}
  .abs{position:absolute}

  /* header */
  .site-header{left:0;top:0;width:1200px;height:124px;border-top:4px solid var(--teal);background:var(--white)}
  .main-nav{left:76px;top:52px;display:flex;align-items:center;font-size:11px;font-weight:700;color:var(--ink);letter-spacing:.2px}
  .main-nav span{padding:0 11px}
  .main-nav span:first-child{padding-left:0;color:var(--teal)}
  .main-nav i{font-style:normal;color:var(--ink)}
  .brand{left:0;width:1200px;top:44px;display:flex;justify-content:center;align-items:center;gap:10px}
  .brand-dot{width:16px;height:16px;border-radius:50%;background:var(--green)}
  .brand-name{font-size:22px;font-weight:600;color:var(--ink)}
  .account-nav{left:780px;top:52px;display:flex;align-items:center;font-size:11px;font-weight:700;color:var(--ink)}
  .account-nav .item{display:flex;align-items:center;gap:5px;padding:0 8px}
  .account-nav i{font-style:normal}
  .lang{left:1058px;top:53px;display:flex;align-items:center;gap:8px;font-size:11px;color:var(--ink)}
  .lang-flag{width:22px;height:13px;background:#2f4a8f;border:1px solid #c9cfdc}

  /* hero */
  .hero{left:0;top:124px;width:1200px;height:353px;background:linear-gradient(100deg,#8a4a36 0%,#d9cdb9 22%,#efe6d6 40%,#c7a77a 60%,#5f8fd0 78%,#4a82d6 100%)}

  /* intro choice */
  .section-title{font-size:25px;font-weight:600;color:var(--ink);text-align:center}
  .choice-box{top:576px;width:513px;height:304px;border:1px solid var(--line)}
  .choice-card{top:13px;width:229px;height:274px;border:1px solid var(--line);background:var(--white)}
  .choice-photo{width:227px;height:172px}
  .choice-label{height:100px;display:flex;align-items:center;justify-content:center;text-align:center;font-size:17px;font-weight:700;color:var(--teal);line-height:24px;padding:0 14px}

  /* listings */
  .listing{width:513px;height:186px;background:var(--panel)}
  .listing-photo{left:18px;top:19px;width:168px;height:148px}
  .listing-body{left:202px;top:22px;width:295px;font-size:13px;line-height:23px}
  .listing-title{font-size:17px;font-weight:600;color:var(--teal);line-height:24px}
  .listing-body b{color:#444;font-weight:700}
  .yes{color:var(--green);font-weight:700}
  .button{height:45px;background:var(--green);color:var(--white);font-size:13px;font-weight:700;display:flex;align-items:center;justify-content:center;letter-spacing:.3px}

  /* selling points */
  .selling{left:0;top:1399px;width:1200px;height:334px;background:var(--panel)}
  .selling-divider{left:600px;top:46px;width:1px;height:240px;background:var(--line)}
  .block-title{font-size:24px;font-weight:600;color:var(--ink);line-height:32px;letter-spacing:.3px}
  .tick-list{list-style:none;font-size:14px;color:#444}
  .tick-list li{position:relative;padding-left:26px;height:36px;line-height:20px}
  .tick-list li::before{content:"";position:absolute;left:0;top:4px;width:12px;height:12px;border-radius:50%;background:var(--green)}
  .tick-list li::after{content:"";position:absolute;left:3px;top:6px;width:5px;height:3px;border-left:2px solid var(--white);border-bottom:2px solid var(--white);transform:rotate(-45deg)}

  /* faq */
  .faq-title{left:0;width:1200px;top:1773px;text-align:center;font-size:24px;font-weight:600;color:var(--ink);letter-spacing:.4px}
  .faq-item{left:74px;width:1052px;height:77px;border:1px solid var(--line);display:flex}
  .faq-num{width:64px;background:var(--teal);color:var(--white);font-size:22px;font-weight:700;display:flex;align-items:center;justify-content:center;flex:none}
  .faq-text{padding:12px 18px;font-size:14px;line-height:24px;color:#555}
  .faq-text a{color:var(--teal);font-weight:700;text-decoration:none}

  /* bottom panels */
  .panel{top:2197px;width:513px;height:263px;background:var(--panel);padding:24px 24px}
  .panel .block-title{margin-bottom:16px}
  .panel .tick-list li{height:36px}
  .panel p{font-size:14px;line-height:26px;color:#555}

  /* footer */
  .site-footer{left:0;top:2497px;width:1200px;height:146px;background:var(--footer)}
  .copyright{left:0;width:1200px;top:44px;text-align:center;font-size:12px;color:#9a9a9a}
  .social{left:0;width:1200px;top:83px;display:flex;justify-content:center;gap:16px}
  .social span{width:20px;height:20px;border-radius:3px;background:#9a9a9a}
</style>
</head>
<body>

<header class="site-header abs">
  <nav class="main-nav abs">
    <span>HOME</span><i>|</i><span>ABOUT US</span><i>|</i><span>SERVICES</span><i>|</i><span>FAQ</span><i>|</i><span>CONTACT US</span>
  </nav>
  <div class="brand abs"><span class="brand-dot"></span><span class="brand-name">Harbor Nest Place</span></div>
  <div class="account-nav abs">
    <span class="item"><svg width="11" height="11" viewBox="0 0 11 11"><path d="M1 10 L2 7 L8 1 L10 3 L4 9 Z" fill="var(--green)"/></svg>CREATE</span><i>|</i>
    <span class="item"><svg width="10" height="11" viewBox="0 0 10 11"><path d="M3 5 V3 a2 2 0 0 1 4 0 V5" stroke="var(--green)" stroke-width="1.5" fill="none"/><rect x="1" y="5" width="8" height="6" fill="var(--green)"/></svg>LOG IN</span><i>|</i>
    <span class="item"><svg width="10" height="11" viewBox="0 0 10 11"><circle cx="5" cy="3" r="2.5" fill="var(--green)"/><path d="M0 11 a5 5 0 0 1 10 0 Z" fill="var(--green)"/></svg>MY ACCOUNT</span>
  </div>
  <div class="lang abs"><span class="lang-flag"></span>EN<svg width="8" height="5" viewBox="0 0 8 5"><path d="M1 1 L4 4 L7 1" stroke="#777" fill="none"/></svg></div>
</header>

<div class="hero abs" role="img" aria-label="Photo of townhouse facades with balconies under a blue sky"></div>

<h2 class="section-title abs" style="left:74px;width:513px;top:523px">Searching for Accommodation</h2>
<h2 class="section-title abs" style="left:613px;width:513px;top:523px">I have a House for Rent</h2>

<div class="choice-box abs" style="left:74px">
  <div class="choice-card abs" style="left:13px">
    <div class="choice-photo" role="img" aria-label="Photo of a furnished living room" style="background:linear-gradient(160deg,#cbb79c,#6f5a48)"></div>
    <div class="choice-label">I want to rent a room right now</div>
  </div>
  <div class="choice-card abs" style="left:269px">
    <div class="choice-photo" role="img" aria-label="Photo of young flatmates relaxing at home" style="background:linear-gradient(160deg,#f1efe6,#d8c98f)"></div>
    <div class="choice-label">I want to join<br>a group</div>
  </div>
</div>
<div class="choice-box abs" style="left:613px">
  <div class="choice-card abs" style="left:13px">
    <div class="choice-photo" role="img" aria-label="Photo of a laptop showing an advertising graphic" style="background:linear-gradient(160deg,#dfe3e8,#7c8794)"></div>
    <div class="choice-label">I want<br>to advertise</div>
  </div>
  <div class="choice-card abs" style="left:269px">
    <div class="choice-photo" role="img" aria-label="Photo of a person receiving house keys" style="background:linear-gradient(160deg,#b0473a,#e6c7b0)"></div>
    <div class="choice-label">Why is flatsharing interesting for me?</div>
  </div>
</div>

<article class="listing abs" style="left:74px;top:914px">
  <div class="listing-photo abs" role="img" aria-label="Photo of a group of young workers" style="background:linear-gradient(160deg,#b9aa98,#6d7a86)"></div>
  <div class="listing-body abs">
    <div class="listing-title">Nice Group</div>
    <div>Young workers seeking for accommodation downtown.</div>
    <div><b>Avarage Age:</b> 35yrs</div>
    <div style="margin-top:3px">Men Women Welcome</div>
  </div>
</article>
<article class="listing abs" style="left:74px;top:1117px">
  <div class="listing-photo abs" role="img" aria-label="Photo of young women students together" style="background:linear-gradient(160deg,#d7cdbe,#9a7b60)"></div>
  <div class="listing-body abs" style="top:16px">
    <div class="listing-title">Nice Group</div>
    <div style="line-height:20px">Young ladies studing at University seeking for accommodation close to Brussel University</div>
    <div style="margin-top:2px"><b>Avarage Age:</b> 20years</div>
    <div style="margin-top:2px">Women Only</div>
  </div>
</article>
<article class="listing abs" style="left:613px;top:914px">
  <div class="listing-photo abs" role="img" aria-label="Photo of a detached house with a lawn" style="background:linear-gradient(180deg,#8e5d4a 0%,#dfe3e6 45%,#5f9b3a 100%)"></div>
  <div class="listing-body abs">
    <div class="listing-title">House</div>
    <div><b>Town:</b> 42 Linden Row,Carlow</div>
    <div><b>Rent per month:</b> $300</div>
    <div style="margin-top:4px"><b>Availbility:</b> <span class="yes">Yes</span></div>
  </div>
</article>
<article class="listing abs" style="left:613px;top:1117px">
  <div class="listing-photo abs" role="img" aria-label="Photo of an apartment building" style="background:linear-gradient(160deg,#7fa9d9,#d8b48a 55%,#8a6a4c)"></div>
  <div class="listing-body abs" style="top:26px">
    <div class="listing-title">Appartment</div>
    <div><b>Town:</b> 42 Linden Row,Carlow</div>
    <div><b>Rent per month:</b> $300</div>
    <div style="margin-top:4px"><b>Availbility:</b> <span class="yes">Yes</span></div>
  </div>
</article>

<div class="button abs" style="left:74px;top:1322px;width:513px">SEE MORE GROUPS</div>
<div class="button abs" style="left:613px;top:1322px;width:513px">SEE MORE HOUSES</div>

<section class="selling abs">
  <div class="selling-divider abs"></div>
  <div class="abs" style="left:74px;top:40px;width:500px">
    <h3 class="block-title">KEY SELLING POINTS FOR<br>THE ROOMMATES</h3>
    <ul class="tick-list" style="margin-top:22px">
      <li>Aliquam molestie, mi et imperdiet euismod.</li>
      <li>Dui purus auctor tellus, et interdum lacus lectus et ante.</li>
      <li>Sed accumsan sollicitudin sapien, sit amet adipiscing turpis.</li>
      <li>Neque ac lobortis volutpat, libero mauris varius mi.</li>
      <li>Vitae suscipit ipsum ligula vitae risus.</li>
    </ul>
  </div>
  <div class="abs" style="left:659px;top:40px;width:500px">
    <h3 class="block-title">KEY SELLING POINTS FOR<br>THE OWNERS</h3>
    <ul class="tick-list" style="margin-top:22px">
      <li>Aliquam molestie, mi et imperdiet euismod.</li>
      <li>Dui purus auctor tellus, et interdum lacus lectus et ante.</li>
      <li>Sed accumsan sollicitudin sapien, sit amet adipiscing turpis.</li>
      <li>Neque ac lobortis volutpat, libero mauris varius mi.</li>
      <li>Vitae suscipit ipsum ligula vitae risus.</li>
    </ul>
  </div>
</section>

<h2 class="faq-title abs">EVERYTHING YOU NEED TO KNOW ABOUT FLATSHARING</h2>
<div class="faq-item abs" style="top:1832px"><div class="faq-num">1.</div><div class="faq-text">Aliquam molestie, mi et imperdiet euismod, dui purus auctor tellus, et interdum lacus lectus et ante. Sed accumsan sollicitudin sapien, sit amet adipiscing turpis gravida ac. In congue, neque ac lobortis volutpat, libero mauris varius mi...<a>Read More</a></div></div>
<div class="faq-item abs" style="top:1918px"><div class="faq-num">2.</div><div class="faq-text">Aliquam molestie, mi et imperdiet euismod, dui purus auctor tellus, et interdum lacus lectus et ante. Sed accumsan sollicitudin sapien, sit amet adipiscing turpis gravida ac. In congue, neque ac lobortis volutpat, libero mauris varius mi...<a>Read More</a></div></div>
<div class="faq-item abs" style="top:2005px"><div class="faq-num">3.</div><div class="faq-text">Aliquam molestie, mi et imperdiet euismod, dui purus auctor tellus, et interdum lacus lectus et ante. Sed accumsan sollicitudin sapien, sit amet adipiscing turpis gravida ac. In congue, neque ac lobortis volutpat, libero mauris varius mi...<a>Read More</a></div></div>

<div class="button abs" style="left:344px;top:2112px;width:512px">ALL QUESTIONS</div>

<section class="panel abs" style="left:74px">
  <h3 class="block-title">PRE-DEFINED SEARCHES</h3>
  <ul class="tick-list">
    <li>Aliquam molestie, mi et imperdiet euismod.</li>
    <li>Dui purus auctor tellus, et interdum lacus lectus et ante.</li>
    <li>Sed accumsan sollicitudin sapien, sit amet adipiscing turpis.</li>
    <li>Neque ac lobortis volutpat, libero mauris varius mi.</li>
    <li>Vitae suscipit ipsum ligula vitae risus.</li>
  </ul>
</section>
<section class="panel abs" style="left:613px">
  <h3 class="block-title">TOOLS &amp; INFORMATIONS</h3>
  <p>Aliquam molestie, mi et imperdiet euismod, dui purus auctor tellus, et interdum lacus lectus et ante. Sed accumsan sollicitudin sapien, sit amet adipiscing turpis gravida ac. In congue, neque ac lobortis volutpat, libero mauris varius mi, vitae suscipit ipsum ligula vitae risus. Suspendisse lobortis turpis in odio blandit ac interdum lorem euismod.</p>
</section>

<footer class="site-footer abs">
  <div class="copyright abs">Copyright © 2016. Company Name. All Rights Reserved.</div>
  <div class="social abs"><span></span><span></span><span></span><span></span><span></span></div>
</footer>

</body>
</html>
```